real esate business card with company logo and name

we need a business card design for a real esate company

The company name is Walsh & Brand Pty Ltd, and we have our logo designed and will upload. We want classic or moden feel. Black or white background. looks more textured. Should include folowinginformations
Owen Walsh and Lucy Brand
Sales Agents & Onsite Manager
p: 07 5948 2063
F: 07 5948 2174
M:0431 857 219
3/42 Marlow Crescent, FERNLEA QLD 4213

We want this business card looks professonal. Thank you in advance.

Industry/Entity Type

Real Estate Agent

Contact Information for Business Card

Owen Walsh and Lucy Brand
Onsite Manager & Sales Agents
p: 07 5948 2063
M:0431 857 219

Font styles to use
Serif

Colors
000000
fbfbfb
333333
959595

Requirements
Must have
• company logo and name, black or white back ground

```html
<!DOCTYPE html>
<html lang="en">
<head>
<meta charset="utf-8">
<title>Walsh &amp; Brand Pty Ltd – Business Cards</title>
<link rel="stylesheet" href="https://fonts.googleapis.com/css2?family=Tinos:ital,wght@0,400;0,700;1,400&display=swap">
<style>
  :root {
    --black: #000000;
    --off-white: #fbfbfb;
    --charcoal: #333333;
    --grey: #959595;
    --canvas: #eeeeee;
    --card-dark: #1c1c1c;
  }
  * { margin: 0; padding: 0; box-sizing: border-box; }
  html, body {
    width: 1200px; height: 1200px; overflow: hidden;
    background: var(--canvas);
    font-family: "Tinos", "Times New Roman", serif;
  }
  .sheet {
    position: relative; width: 1200px; height: 1200px;
  }
  .card {
    position: absolute; left: 220px;
    width: 760px; height: 434px;
    overflow: hidden;
    box-shadow: 0 10px 30px rgba(0,0,0,0.12);
  }
  .card--light { top: 130px; background: var(--off-white); color: var(--charcoal); }
  .card--dark  { top: 636px; background: var(--card-dark); color: var(--off-white); }

  .card__stripes { position: absolute; top: 0; left: 0; width: 100%; }
  .card__stripes span { display: block; width: 100%; }
  .card--light .stripe-a { height: 14px; background: var(--charcoal); }
  .card--light .stripe-b { height: 10px; background: var(--grey); }
  .card--dark .stripe-a  { height: 14px; background: var(--grey); }
  .card--dark .stripe-b  { height: 10px; background: var(--charcoal); }

  .brand {
    position: absolute; left: 70px; top: 110px;
    display: flex; align-items: center; gap: 14px;
  }
  .brand__mark { width: 44px; height: 44px; background: var(--grey); }
  .brand__name {
    font-size: 20px; font-weight: 400; letter-spacing: 1px;
    text-transform: uppercase; color: var(--grey);
  }

  .contact {
    position: absolute; left: 370px; top: 190px;
    font-size: 19px; line-height: 29px;
  }
  .contact__names { font-weight: 700; font-size: 24px; line-height: 32px; }
  .contact__role  { font-style: italic; font-size: 21px; margin-bottom: 2px; }
  .card--light .contact__names { color: var(--black); }
</style>
</head>
<body>
<main class="sheet">
  <section class="card card--light" aria-label="Business card, white front">
    <div class="card__stripes"><span class="stripe-a"></span><span class="stripe-b"></span></div>
    <div class="brand">
      <span class="brand__mark"></span>
      <span class="brand__name">Walsh &amp; Brand Pty Ltd</span>
    </div>
    <div class="contact">
      <p class="contact__names">Owen Walsh and Lucy Brand</p>
      <p class="contact__role">Onsite Manager &amp; Sales Agents</p>
      <p>p: 07 5948 2063</p>
      <p>M:0431 857 219</p>
      <p>3/42 Marlow Crescent,</p>
      <p>FERNLEA QLD 4213</p>
    </div>
  </section>

  <section class="card card--dark" aria-label="Business card, black back">
    <div class="card__stripes"><span class="stripe-a"></span><span class="stripe-b"></span></div>
    <div class="brand">
      <span class="brand__mark"></span>
      <span class="brand__name">Walsh &amp; Brand Pty Ltd</span>
    </div>
    <div class="contact">
      <p class="contact__names">Owen Walsh and Lucy Brand</p>
      <p class="contact__role">Onsite Manager &amp; Sales Agents</p>
      <p>p: 07 5948 2063</p>
      <p>M:0431 857 219</p>
      <p>3/42 Marlow Crescent,</p>
      <p>FERNLEA QLD 4213</p>
    </div>
  </section>
</main>
</body>
</html>
```